Web Design Velmora Tech

• An Overview of Velmora Tech for reference: We use to be a component manufacturing company. We sold to customers in USA and manage the builds in China using many manufacturing partners. We had a web site that served this market but we have transitioned over the last several years into “A unique design, development and program management company” It is this message we want to put up on the web now. We provide the design support, we help develop and test a new product for our customers and we provide the manufactured produce once we have transitioned it into production.
• The Target Market: Our customers are all high tech. Each product we produce is custom designed and sold only to one a specific customer. We work with a limited number of customer and sell to new customers by word of mouth and referrals. The web site is to provide a back ground check of any new referral so they can see who we are and our basic capabilities. It is not designed to sell customers or to find new customers but provide a background check to new potential customers.
• Pages Required: We estimate 12:
o Home/Title page is page 1 of PDF. It would have buttons to select other pages
o Names of other pages would be (short titles below if on button, if pull down menu the full title of slide)
 USA Facilities
 China Facilities
 Enclosures
 Antennas
 Connectors
 Cables
 EMI Shields
 Overlays
 Process Development
 BrisaLink
 Contact Us (???) >> new page which we are not sure if we should or should not add.
• Design Specifics; attached is our logo, a PDF and PowerPoint slides showing the views we desire. We like these layouts, but perhaps a better one may be suggested for some artistic reason or layout. It should be clean, simple and user intuitive. We like the off white background and use for most of our presentations. One should be able to go from any screen to any other screen. The quote must include both design and implementation onto our web site which is http://velmoratechworks.example/
• Design Process:
We would like to see concepts of the Landing/Homepage, and an internal page initially. Feedback will be provided and you will be asked to continue if your layout is on the correct track.

• Implementation: Desire designer/implimentor to set up on their server. Allow us to test and edit on their site. We will provide password for implementation on our site after final approval.

Target Market(s)

• The Target Market: see above task descripiton

Industry/Entity Type

It Company

Requirements
Must have
• • Pages Required: We estimate 12:
 USA Facilities
 China Facilities
 Enclosures
 Antennas
 Connectors
 Cables
 EMI Shields
 Overlays
 Process Development
 BrisaLink

Must have the implementation phase include in quote. see task description above
Should not have
• Should not be complex or long time loading.
Do not want any twitter or promotional add on functions.

```html
<!DOCTYPE html>
<html lang="en">
<head>
<meta charset="utf-8">
<title>Velmora Tech – Process Development</title>
<link href="https://fonts.googleapis.com/css2?family=Signika:wght@300;400;600&display=swap" rel="stylesheet">
<style>
:root{
  --page-bg:#f6f6f4;
  --footer-bg:#e3e3e3;
  --brand-blue:#0a6fbf;
  --panel-top:#5a5a5a;
  --panel-bottom:#2f2f2f;
  --text:#565656;
  --text-dark:#333;
  --white:#ffffff;
  --divider:#b9b9b9;
}
*{margin:0;padding:0;box-sizing:border-box}
html,body{width:1200px;height:1121px;overflow:hidden}
body{background:var(--page-bg);font-family:"Signika",sans-serif;color:var(--text);position:relative}
.abs{position:absolute}

.addresses{top:20px;right:90px;display:flex;font-size:14.5px;line-height:23px;color:var(--text)}
.addresses .office{padding:0 16px;text-align:right}
.addresses .office + .office{border-left:1px solid var(--divider);text-align:left;padding-right:0}

.brand{left:90px;top:80px;width:208px;height:209px;display:flex;align-items:center;gap:10px}
.brand-mark{width:22px;height:22px;background:var(--brand-blue);flex:none}
.brand-name{font-weight:600;font-size:32px;line-height:36px;color:var(--brand-blue)}

.main-nav{left:90px;top:300px;width:208px;height:470px;background:linear-gradient(var(--panel-top),var(--panel-bottom));padding-top:16px}
.main-nav a{display:flex;align-items:center;height:37.6px;padding-left:20px;color:var(--white);text-decoration:none;font-size:14.5px;font-weight:300}
.main-nav a.current{font-weight:400}
.main-nav svg{margin-right:16px}

.contact-card{left:90px;top:780px;width:208px;height:219px;background:linear-gradient(var(--panel-top),var(--panel-bottom));color:var(--white);padding:14px 12px}
.contact-head{display:flex;gap:8px;align-items:center}
.contact-head h2{font-size:22px;font-weight:400;line-height:26px}
.phone-icon{width:44px;height:44px;border-radius:50%;background:#111;display:flex;align-items:center;justify-content:center;flex:none}
.contact-card dl{margin-top:14px;font-size:16.5px;line-height:33px}
.contact-card .email{font-size:13px;line-height:16px}

.hero{left:314px;top:80px;width:797px;height:452px;border:3px solid #444;background:linear-gradient(135deg,#9a8a74,#7a6b5a 45%,#c9c4bb 70%,#b48e62)}
.hero-caption{position:absolute;left:0;right:0;bottom:0;height:95px;background:rgba(30,30,30,.82);color:var(--white);font-size:19px;font-weight:600;line-height:29px;padding:20px 28px}
.hero-next{position:absolute;right:24px;top:34px;width:28px;height:28px;border-radius:50%;background:var(--white);display:flex;align-items:center;justify-content:center}

.content{left:314px;top:552px;width:458px}
.content h1{font-size:23px;font-weight:400;color:var(--brand-blue);margin-bottom:10px}
.content p{font-size:14.5px;line-height:25px;text-align:justify}
.content h3{margin-top:14px;font-size:15.5px;font-weight:600;color:var(--brand-blue)}

.photo{border:3px solid #d8d8d8}
.photo-adhesive-operator{left:316px;top:814px;width:240px;height:183px;background:linear-gradient(160deg,#c9cdd0,#8d939a 60%,#5d6670)}
.photo-adhesive-part{left:579px;top:814px;width:239px;height:183px;background:radial-gradient(circle at 45% 55%,#222 0 28%,#a9adb0 30%,#cfd2d3)}
.photo-test-station{left:822px;top:595px;width:288px;height:402px;border:none;background:linear-gradient(90deg,#c9d3d8,#e7ecee 40%,#e9e8e4)}
.photo-test-station span{position:absolute;left:145px;top:256px;width:130px;text-align:center;font-size:15px;line-height:23px;color:var(--text-dark);font-weight:400}

.site-footer{left:0;top:1028px;width:1200px;height:93px;background:var(--footer-bg);text-align:center;font-size:13.5px;color:var(--text-dark)}
.footer-nav{margin-top:22px}
.footer-nav a{color:var(--text-dark);text-decoration:none;padding:0 7px}
.footer-nav a + a{border-left:1px solid var(--text-dark)}
.copyright{margin-top:16px;font-size:13.5px}
</style>
</head>
<body>

<div class="abs addresses">
  <div class="office">48 Larkspur Road, Unit 12<br>Fairhaven, CA - 90210</div>
  <div class="office">Eastgate District, Lantern Road #17<br>Riverbend, China - 100099</div>
</div>

<div class="abs brand">
  <span class="brand-mark"></span>
  <span class="brand-name">Velmora Tech</span>
</div>

<nav class="abs main-nav">
  <a class="current" href="#"><svg width="6" height="10"><path d="M1 1l4 4-4 4" stroke="#fff" stroke-width="2" fill="none"/></svg>Home</a>
  <a href="#"><svg width="6" height="10"><path d="M1 1l4 4-4 4" stroke="#fff" stroke-width="2" fill="none"/></svg>USA Facilities</a>
  <a href="#"><svg width="6" height="10"><path d="M1 1l4 4-4 4" stroke="#fff" stroke-width="2" fill="none"/></svg>China Facilities</a>
  <a href="#"><svg width="6" height="10"><path d="M1 1l4 4-4 4" stroke="#fff" stroke-width="2" fill="none"/></svg>Enclosures</a>
  <a href="#"><svg width="6" height="10"><path d="M1 1l4 4-4 4" stroke="#fff" stroke-width="2" fill="none"/></svg>Antennas</a>
  <a href="#"><svg width="6" height="10"><path d="M1 1l4 4-4 4" stroke="#fff" stroke-width="2" fill="none"/></svg>Connectors</a>
  <a href="#"><svg width="6" height="10"><path d="M1 1l4 4-4 4" stroke="#fff" stroke-width="2" fill="none"/></svg>Cables</a>
  <a href="#"><svg width="6" height="10"><path d="M1 1l4 4-4 4" stroke="#fff" stroke-width="2" fill="none"/></svg>EMI Shields</a>
  <a href="#"><svg width="6" height="10"><path d="M1 1l4 4-4 4" stroke="#fff" stroke-width="2" fill="none"/></svg>Overlays</a>
  <a href="#"><svg width="6" height="10"><path d="M1 1l4 4-4 4" stroke="#fff" stroke-width="2" fill="none"/></svg>Process Development</a>
  <a href="#"><svg width="6" height="10"><path d="M1 1l4 4-4 4" stroke="#fff" stroke-width="2" fill="none"/></svg>BrisaLink</a>
  <a href="#"><svg width="6" height="10"><path d="M1 1l4 4-4 4" stroke="#fff" stroke-width="2" fill="none"/></svg>Contact Us</a>
</nav>

<aside class="abs contact-card">
  <div class="contact-head">
    <span class="phone-icon"><svg width="22" height="26" viewBox="0 0 22 26"><path d="M6 2c-3 1-5 4-4 9 1 6 6 12 11 13 3 1 5-1 6-3l-4-4-3 2c-3-2-5-5-6-8l3-2z" fill="#fff"/></svg></span>
    <h2>Contact<br>Velmora Tech</h2>
  </div>
  <dl>
    <div>Call us : 555 014 2287</div>
    <div>Fax &nbsp;&nbsp;: 555 014 2290</div>
    <div>Email</div>
    <div class="email">info@velmoratechworks.example</div>
  </dl>
</aside>

<section class="abs hero" role="img" aria-label="Three engineers discussing enclosure prototypes at a table with a CAD model on screen">
  <div class="hero-caption">A unique design, development and program<br>management company
    <span class="hero-next"><svg width="8" height="12"><path d="M2 1l5 5-5 5" stroke="#333" stroke-width="2.4" fill="none"/></svg></span>
  </div>
</section>

<main class="abs content">
  <h1>Process Development</h1>
  <p>Morbi porttitor arcu quis sapien porttitor faucibus. Nullam bibendum viverra lorem, luctus suscipit nulla facilisis in. Donec euismod magna quam, quis semper tortor luctus vel. Quisque erat erat, ornare eget pretium eget, hendrerit id magna. Cras dolor quam, faucibus id placerat a, mattis eu elit. Praesent ac lobortis nisl. Integer volutpat tempor eros vitae pulvinar. Praesent nec est iaculis, tincidunt mauris in, vehicula orci. Sed placerat felis risus, ut imperdiet augue adipiscing ac.</p>
  <h3>Automated adhesive application</h3>
</main>

<div class="abs photo photo-adhesive-operator" role="img" aria-label="Technician operating an automated adhesive dispensing machine"></div>
<div class="abs photo photo-adhesive-part" role="img" aria-label="Close-up of adhesive being applied to a round black part"></div>
<div class="abs photo photo-test-station" role="img" aria-label="Water submersion testing station with gauges and a clear tank">
  <span>Water submersion testing station – vacuum &amp; pressure</span>
</div>

<footer class="abs site-footer">
  <nav class="footer-nav">
    <a href="#">Home</a><a href="#">USA Facilities</a><a href="#">China Facilities</a><a href="#">Enclosures</a><a href="#">Antennas</a><a href="#">Connectors</a><a href="#">Cables</a><a href="#">EMI Shields</a><a href="#">Overlays</a><a href="#">Process Development</a><a href="#">BrisaLink</a><a href="#">Contact Us</a>
  </nav>
  <p class="copyright">Copyright © 2013 &nbsp;Velmora Technologies. &nbsp;&nbsp;All rights reserved.</p>
</footer>

</body>
</html>
```